Healthcare and Professional IT Services Company need a redesigned business card

We are a IT Services company that targets small medical practices and professional business such as Attorneys, Accounts, Architects etc. We want to communicate a professional yet friendly image using recent logo redesign here on ArtHarbor. Like to see the colors blue and orange in the design. Must use the Tall Pine Computing as displayed in the new logo - then also want to incorporate the fish logo as well.

Target Market(s)

Small medical and professional services

Industry/Entity Type

It Company

Contact Information for Business Card

The usual stuff, place for name address phone website. Also maybe our tagline which is "rooted in smart support"

Requirements
Must have
• My new logo and the fish somewhere on the card

```html
<!DOCTYPE html>
<html lang="en">
<head>
<meta charset="UTF-8">
<title>Tall Pine Computing – Business Card</title>
<link href="https://fonts.googleapis.com/css2?family=Tinos:wght@400;700&display=swap" rel="stylesheet">
<style>
  :root {
    --page-bg: #e9e7e3;
    --card-white: #f7f7f5;
    --corner-blue: #6f86c2;
    --ink: #1c1c1c;
    --brand-cyan: #1fb4e0;
    --brand-sky: #8fcbe6;
    --card-black: #0b0b0c;
    --art-orange: #e0793a;
    --art-teal: #5aa3c4;
  }
  * { box-sizing: border-box; margin: 0; padding: 0; }
  html, body {
    width: 1200px; height: 892px; overflow: hidden;
    background: var(--page-bg);
    font-family: "Tinos", "Times New Roman", serif;
    color: var(--ink);
  }
  .canvas {
    width: 1200px; height: 892px;
    display: flex; flex-direction: column;
    align-items: center; justify-content: center; gap: 44px;
  }
  .card {
    position: relative;
    width: 660px; height: 377px;
    border-radius: 22px;
    overflow: hidden;
    box-shadow: 0 6px 18px rgba(0,0,0,.18);
  }

  /* front */
  .card-front { background: var(--corner-blue); }
  .card-front .face {
    position: absolute; inset: 0;
    background: var(--card-white);
    clip-path: polygon(17% 0, 83% 0, 100% 50%, 83% 100%, 17% 100%, 0 50%);
  }
  .brand-row {
    position: absolute; top: 54px; left: 0; right: 0;
    display: flex; align-items: center; justify-content: center; gap: 18px;
  }
  .fish-art {
    width: 92px; height: 66px; border-radius: 40% 50% 45% 40%;
    background: linear-gradient(135deg, var(--art-teal), var(--art-orange));
  }
  .wordmark {
    font-size: 40px; font-weight: 700; color: var(--brand-sky);
    letter-spacing: .5px;
  }
  .details {
    position: absolute; top: 168px; left: 0; right: 0;
    display: flex; justify-content: center; align-items: stretch;
  }
  .person-name {
    font-size: 34px; padding: 18px 24px 14px 0;
    border-right: 2px solid var(--ink);
    align-self: flex-end;
  }
  .contact-list { list-style: none; padding-left: 18px; font-size: 19px; line-height: 1.35; }
  .contact-list li { display: flex; align-items: flex-start; gap: 10px; }
  .contact-list svg { width: 16px; height: 16px; margin-top: 4px; flex: none; }
  .tagline {
    position: absolute; bottom: 40px; left: 0; right: 0;
    text-align: center; font-size: 17px;
  }

  /* back */
  .card-back {
    background: linear-gradient(135deg, #1b1b1d 0%, var(--card-black) 55%);
    display: flex; align-items: center; justify-content: center; gap: 34px;
  }
  .back-art {
    width: 170px; height: 150px; border-radius: 45% 50% 40% 48%;
    background: radial-gradient(circle at 40% 45%, #123a4a, #0a1c24);
    border: 3px solid var(--brand-cyan);
  }
  .back-brand { display: flex; align-items: center; gap: 12px; }
  .back-brand .dot { width: 14px; height: 14px; border-radius: 50%; background: var(--art-orange); }
  .back-wordmark { font-size: 40px; font-weight: 700; color: var(--brand-cyan); }
</style>
</head>
<body>
<main class="canvas">
  <section class="card card-front" aria-label="Card front">
    <div class="face">
      <div class="brand-row">
        <div class="fish-art" role="img" aria-label="Colourful cartoon fish illustration"></div>
        <span class="wordmark">Tall Pine Computing</span>
      </div>
      <div class="details">
        <p class="person-name">Jordan Reyes</p>
        <ul class="contact-list">
          <li>
            <svg viewBox="0 0 16 16" aria-hidden="true"><rect width="16" height="16" rx="2" fill="#1c1c1c"/><path d="M5 3.5l2 2-1.2 1.2c.6 1.4 1.6 2.4 3 3L10 8.5l2 2-1.4 1.6C7 11.5 4.5 9 3.9 5.4z" fill="#fff"/></svg>
            <span>480-555-0142</span>
          </li>
          <li>
            <svg viewBox="0 0 16 16" aria-hidden="true"><rect width="16" height="16" rx="2" fill="#1c1c1c"/><circle cx="8" cy="8" r="4.5" fill="none" stroke="#fff" stroke-width="1.2"/><path d="M3.5 8h9M8 3.5c-2 2.5-2 6.5 0 9M8 3.5c2 2.5 2 6.5 0 9" fill="none" stroke="#fff" stroke-width="1"/></svg>
            <span>www.tallpinecomputing.com</span>
          </li>
          <li>
            <svg viewBox="0 0 16 16" aria-hidden="true"><rect width="16" height="16" rx="2" fill="#1c1c1c"/><path d="M8 2.8a3.4 3.4 0 0 0-3.4 3.4C4.6 9 8 13 8 13s3.4-4 3.4-6.8A3.4 3.4 0 0 0 8 2.8z" fill="#fff"/><circle cx="8" cy="6.2" r="1.2" fill="#1c1c1c"/></svg>
            <span>1820 W. Harbor Lane Tempe,<br>Arizona 85281</span>
          </li>
        </ul>
      </div>
      <p class="tagline">Also maybe our tagline which is "rooted in smart support"</p>
    </div>
  </section>

  <section class="card card-back" aria-label="Card back">
    <div class="back-art" role="img" aria-label="Outlined cartoon fish illustration in cyan"></div>
    <div class="back-brand">
      <span class="dot"></span>
      <span class="back-wordmark">Tall Pine Computing</span>
    </div>
  </section>
</main>
</body>
</html>
```